Environmental Plastics Infographic on Marine Debris

We need a series of infographics that can be used individually or as a combined presentation. We'd like the combined piece to include an introduction and conclusion along with 4-5 infographics. Each infographic (information unit) should also work as a standalone. We are trying to help people visualize size proportions and ratios to put the plastics marine debris problem in perspective. Our key point is concerning polystyrene foam which represents 35 tons. We are looking for something creative to help people understand what the problem represents in terms they are familiar with.

To view our typical company design/style please see our website at www.harbenfieldgroup.org. Our primary RGB colors are: (187,140,9); (94,47,29); (94,138,164); and (164,167,15). Secondary RGB colors are (249,162,28) and (218,210,208). Our title/header font is DIN Next LT Pro and our copy font is Calibri 10.5 pt. We can deviate from the font specification if beneficial and welcome interesting text treatments and typography.

Need extra days to review

Target Market(s)

international brand manufacturers (brightmoor, kavo), US legislators & government agencies

Font styles to use
Sans Serif

Requirements
Must have
• Sufficient white space. Easy to grasp message concept with visual components.

```html
<!DOCTYPE html>
<html lang="en">
<head>
<meta charset="utf-8">
<title>Plastic Weight Comparison</title>
<link rel="stylesheet" href="https://fonts.googleapis.com/css2?family=Open+Sans:wght@400;700&display=swap">
<style>
  :root {
    --orange: #f7a21e;
    --orange-deep: #f47b20;
    --hex-grey: #dad4d2;
    --card: #f3eeee;
    --navy: #0e2a36;
    --line: #f3eeee;
  }
  html, body {
    margin: 0;
    padding: 0;
    width: 1200px;
    height: 899px;
    overflow: hidden;
    background: var(--orange);
  }
  .infographic {
    display: block;
    width: 1200px;
    height: 899px;
    font-family: "Open Sans", "Segoe UI", sans-serif;
  }
  .hex { fill: var(--hex-grey); }
  .connector { stroke: var(--line); stroke-width: 10; }
  .card { fill: var(--card); }
  .card-label { fill: var(--navy); font-size: 31px; text-anchor: middle; letter-spacing: 0.5px; }
  .card-sublabel { fill: var(--navy); font-size: 24px; text-anchor: middle; }
  .card-value { fill: var(--navy); font-size: 50px; font-weight: 700; text-anchor: middle; }
  .card-unit { fill: var(--navy); font-size: 50px; text-anchor: middle; }
  .weight-body { fill: var(--navy); }
  .weight-handle { fill: none; stroke: var(--navy); stroke-width: 16; }
  .weight-num { fill: var(--hex-grey); font-size: 46px; text-anchor: middle; }
  .weight-unit { fill: var(--hex-grey); font-size: 22px; text-anchor: middle; }
</style>
</head>
<body>
<svg class="infographic" viewBox="0 0 1501 1125" preserveAspectRatio="none" xmlns="http://www.w3.org/2000/svg">
  <defs>
    <linearGradient id="honeycomb-tone" x1="0" y1="0" x2="1" y2="1">
      <stop offset="0" stop-color="#f8a424"/>
      <stop offset="0.5" stop-color="#f79d1f"/>
      <stop offset="1" stop-color="#f58f20"/>
    </linearGradient>
    <symbol id="weight-shape" viewBox="0 0 100 160">
      <path class="weight-handle" d="M24 72 C10 6 90 6 76 72"/>
      <path class="weight-body" d="M14 58 L86 58 Q100 95 98 150 Q50 160 2 150 Q0 95 14 58 Z"/>
    </symbol>
    <symbol id="weight" viewBox="0 0 100 160">
      <use href="#weight-shape" x="0" y="0" width="100" height="160"/>
      <text class="weight-num" x="50" y="116">50</text>
      <text class="weight-unit" x="50" y="140">TONS</text>
    </symbol>
    <clipPath id="half-top"><rect x="790" y="270" width="54" height="180"/></clipPath>
    <clipPath id="half-left"><rect x="400" y="495" width="22" height="120"/></clipPath>
  </defs>

  <rect class="background" x="0" y="0" width="1501" height="1125" fill="url(#honeycomb-tone)" role="img" aria-label="Honeycomb pattern of orange hexagons"/>

  <g class="hexagons">
    <polygon class="hex hex-gpgp" points="533,358 667,168 863,168 972,358 863,548 667,548"/>
    <polygon class="hex hex-nyc" points="192,555 302,366 522,366 632,555 522,745 302,745"/>
    <polygon class="hex hex-ship" points="873,555 983,364 1203,364 1313,555 1203,745 983,745"/>
    <polygon class="hex hex-whale" points="533,755 667,565 863,565 972,755 863,945 667,945"/>
  </g>

  <g class="connectors">
    <line class="connector" x1="417" y1="208" x2="765" y2="208"/>
    <line class="connector" x1="1250" y1="327" x2="1250" y2="500"/>
    <line class="connector" x1="256" y1="622" x2="256" y2="797"/>
    <line class="connector" x1="735" y1="916" x2="1088" y2="916"/>
  </g>

  <g class="weights weights-gpgp">
    <use href="#weight" x="663" y="278" width="102" height="160"/>
    <g clip-path="url(#half-top)"><use href="#weight-shape" x="793" y="278" width="102" height="160"/></g>
  </g>
  <g class="weights weights-nyc">
    <use href="#weight" x="318" y="441" width="68" height="106"/>
    <use href="#weight" x="437" y="441" width="68" height="106"/>
    <use href="#weight" x="318" y="564" width="68" height="106"/>
    <use href="#weight" x="437" y="564" width="68" height="106"/>
    <g clip-path="url(#half-left)"><use href="#weight-shape" x="402" y="500" width="68" height="106"/></g>
  </g>
  <g class="weights weights-ship">
    <use href="#weight" x="987" y="482" width="93" height="146"/>
    <use href="#weight" x="1110" y="482" width="93" height="146"/>
  </g>
  <g class="weights weights-whale">
    <use href="#weight" x="674" y="641" width="68" height="106"/>
    <use href="#weight" x="763" y="641" width="68" height="106"/>
    <use href="#weight" x="674" y="763" width="68" height="106"/>
    <use href="#weight" x="763" y="763" width="68" height="106"/>
  </g>

  <g class="stat-card">
    <rect class="card" x="95" y="88" width="322" height="239"/>
    <text class="card-label" x="256" y="155">All GPGP Plastics</text>
    <text class="card-value" x="256" y="222">78,908</text>
    <text class="card-unit" x="256" y="287">TONS</text>
  </g>
  <g class="stat-card">
    <rect class="card" x="1088" y="88" width="323" height="239"/>
    <text class="card-label" x="1250" y="153">One Cruise Ship</text>
    <text class="card-value" x="1250" y="220">100,000</text>
    <text class="card-unit" x="1250" y="285">TONS</text>
  </g>
  <g class="stat-card">
    <rect class="card" x="95" y="797" width="322" height="239"/>
    <text class="card-label" x="256" y="838">One Week</text>
    <text class="card-sublabel" x="256" y="873">NYC Waste Generation</text>
    <text class="card-value" x="256" y="938">269,230</text>
    <text class="card-unit" x="256" y="1003">TONS</text>
  </g>
  <g class="stat-card">
    <rect class="card" x="1088" y="797" width="323" height="239"/>
    <text class="card-label" x="1250" y="861">One Blue Whale</text>
    <text class="card-value" x="1250" y="927">200,000</text>
    <text class="card-unit" x="1250" y="992">TONS</text>
  </g>
</svg>
</body>
</html>
```